Hardcore nerd needs to stand out in a sea of dull Defence business cards

Wombarra Devices is a new Australian consulting engineering company that turns research and theory into practical systems. No evangelistic fluff, just mathematics and physics into electronic and optical circuits for consumer products, scientific research or Defence applications.

We already have a recognised logo (provided) which is often dark blue/black on a light background but we're open to other combinations. (Us engineers tend to have limited aesthetic imagination :)

Some of our recent products have included:
* Instrumentation for electrical testing,
* Radar jammers,
* GPS antenna design,
* Satellite tracking systems,
* High power lasers

We're open to both single and double-sided designs - happy to be convinced either way.

P.S. Another group is working on the web page, so - alas - our web site is currently of no use for images/ideas...

Target Market(s)

Engineering managers,
Scientists

Contact Information for Business Card

Dr Colin Harte
R&D Engineer

colin@wombarradevices.com.au
0427 563 710

PO Box XXX (to be confirmed)
Kelsby ACT 2917
Australia

Font styles to use
Serif
Sans Serif

Colors

Designer to choose colors to be used in the design.

Requirements
Must have
• My contact details!
• I've had many (great) "bold and plain" designs submitted already, so feel free to be artistically creative :)
• Happy to take advice re fonts/colours/printability etc.
Nice to have
• I'm not sure if "lists" are more at home on a CV than a business card, but representative services include:
• Applied electromagnetics
• RF and high speed electronics
• Signal and image processing
• Electro-optical and laser systems
• Concept-to-prototype design services
• If you're considering double sided cards, then often measuring/alignment grids/rulers feature on the back of similar cards.
• e.g. https://www.veltranoptics.example/newgrouppage9.cfm?objectgroup_id=4183
• https://www.veltranoptics.example/newgrouppage9.cfm?objectgroup_ID=4185
• ..or even a "Smith chart" (google will return lots)
• Generic images to represent a capability might work - googling images associated with keyword for each of these areas might help:
• - "passive radar", "phased array", "fdtd", "vircator"
• RF and high speed electronic design
• - "smith chart", "microstrip circuits", "dimensioned drawing", "electronic schematic"
• - "dft", "iir filter"
• - "optical cavity". "laser energy level diagram"
• Background/watermarked images outlines/wireframes/schematics would probably look OK.
Should not have
• If a list of projects/services is provided, it is important not to make the client feel that this is "all" the company can do. Engineering design is a creative discipline (like graphics :)
• Please, no stock "military" snaps like planes, missiles, etc!

```html
<!DOCTYPE html>
<html lang="en">
<head>
<meta charset="utf-8">
<title>Wombarra Devices – Business Card</title>
<link rel="stylesheet" href="https://fonts.googleapis.com/css2?family=Montserrat:wght@400;500;700&display=swap">
<style>
  :root {
    --backdrop: #2e251f;
    --paper: #fbfbfa;
    --navy: #1c2a6b;
    --ink-soft: #2a3570;
    --card-black: #141414;
    --card-mid: #2c2c2c;
    --card-grey: #6a6a6a;
    --white: #ffffff;
  }
  * { box-sizing: border-box; margin: 0; padding: 0; }
  html, body {
    width: 1200px; height: 716px; overflow: hidden;
    background: var(--backdrop);
    font-family: "Montserrat", sans-serif;
  }
  .stage { position: relative; width: 1200px; height: 716px; }
  .card {
    position: absolute; top: 210px;
    width: 520px; height: 297px;
    border-radius: 3px;
    box-shadow: 0 14px 30px rgba(0,0,0,.45);
    overflow: hidden;
  }
  /* Front */
  .card-front { left: 50px; background: var(--paper); color: var(--navy); }
  .brand-name {
    position: absolute; left: 34px; top: 28px;
    font-weight: 700; color: var(--navy); line-height: 1.05;
  }
  .brand-name .line-1 { display: block; font-size: 27px; letter-spacing: .5px; }
  .brand-name .line-2 { display: block; font-size: 15px; letter-spacing: 6px; }
  .contact { position: absolute; left: 34px; top: 118px; color: var(--ink-soft); }
  .person-name { font-size: 14px; font-weight: 700; letter-spacing: .3px; }
  .person-role { font-size: 10px; font-weight: 400; margin-top: 2px; }
  .rule { width: 16px; height: 2px; background: var(--navy); margin: 10px 0 12px; }
  .address, .detail { font-size: 10px; line-height: 1.55; font-weight: 400; }
  .detail { display: flex; align-items: center; gap: 6px; }
  .detail svg { width: 9px; height: 9px; fill: var(--navy); flex: none; }
  .address { margin-bottom: 4px; }
  .brand-dot {
    position: absolute; right: 44px; bottom: 34px;
    width: 170px; height: 170px; border-radius: 50%;
    background: var(--navy);
  }
  /* Back */
  .card-back { left: 630px; background: var(--card-black); }
  .back-pattern {
    position: absolute; inset: 0;
    background:
      radial-gradient(ellipse 60% 70% at 88% 75%, rgba(150,150,150,.55) 0%, rgba(150,150,150,0) 70%),
      radial-gradient(ellipse 40% 50% at 70% 25%, rgba(110,110,110,.35) 0%, rgba(110,110,110,0) 70%),
      linear-gradient(120deg, var(--card-black) 0%, #1a1a1a 40%, var(--card-mid) 62%, #4a4a4a 82%, var(--card-grey) 100%);
  }
  .back-lockup {
    position: absolute; left: 168px; top: 128px;
    display: flex; align-items: center; gap: 16px;
    color: var(--white);
  }
  .back-dot {
    width: 58px; height: 58px; border-radius: 50%;
    background: var(--white); flex: none;
  }
  .back-name { font-weight: 700; line-height: 1.1; }
  .back-name .line-1 { display: block; font-size: 26px; letter-spacing: 1px; }
  .back-name .line-2 { display: block; font-size: 14px; letter-spacing: 6px; }
</style>
</head>
<body>
<main class="stage">
  <section class="card card-front" aria-label="Business card front">
    <h1 class="brand-name"><span class="line-1">WOMBARRA</span><span class="line-2">DEVICES</span></h1>
    <div class="contact">
      <p class="person-name">DR COLIN HARTE</p>
      <p class="person-role">R&amp;D Engineer</p>
      <div class="rule"></div>
      <p class="address">PO Box XXX<br>Kelsby ACT 2917, Australia</p>
      <p class="detail">
        <svg viewBox="0 0 24 24" aria-hidden="true"><path d="M6.6 10.8a15.1 15.1 0 0 0 6.6 6.6l2.2-2.2a1 1 0 0 1 1-.25 11.4 11.4 0 0 0 3.6.57 1 1 0 0 1 1 1V20a1 1 0 0 1-1 1A17 17 0 0 1 3 4a1 1 0 0 1 1-1h3.5a1 1 0 0 1 1 1c0 1.25.2 2.45.57 3.6a1 1 0 0 1-.25 1z"/></svg>
        0427 563 710
      </p>
      <p class="detail">
        <svg viewBox="0 0 24 24" aria-hidden="true"><path d="M2 5h20v14H2z"/></svg>
        colin@wombarradevices.com.au
      </p>
    </div>
    <div class="brand-dot" aria-hidden="true"></div>
  </section>

  <section class="card card-back" aria-label="Business card back">
    <div class="back-pattern" role="img" aria-label="Embossed repeating brand pattern in glossy black fading to silver grey"></div>
    <div class="back-lockup">
      <div class="back-dot" aria-hidden="true"></div>
      <p class="back-name"><span class="line-1">WOMBARRA</span><span class="line-2">DEVICES</span></p>
    </div>
  </section>
</main>
</body>
</html>
```